Chomp-iZ Salsa Website

Needing a website to promote and sell our salsa line.

Each tab at the top of our home page will be need to be clickable taking you to another page. Other pages besides the home page include: about us, recipes, buy now, events, contact us.
Updates

Our project brief has been updated to reflect more details.

Coding

Coded - Design and coding required

Number of Pages Required

5+ page

Requirements
Must have
• Follow us on Facelink and Snapgram.

Buy now page will need to have option to add products to shopping chart. We have a PayLo account that will need to linked to shopping chart for payments.

```html
<!DOCTYPE html>
<html lang="en">
<head>
<meta charset="utf-8">
<title>Chomp-iZ Salsa</title>
<link href="https://fonts.googleapis.com/css2?family=Montserrat:wght@400;500;600;700;800&display=swap" rel="stylesheet">
<style>
:root{
  --red:#e31e24;
  --dark:#1b1b1b;
  --ink:#111;
  --white:#fff;
  --star:#e8a33a;
  --olive:#7a9a3a;
  --brown:#2a1512;
  --placeholder-top:#f3ece8;
  --placeholder-bottom:#e2cfc8;
}
*{box-sizing:border-box;margin:0;padding:0}
html,body{width:1200px;height:3392px;overflow:hidden}
body{font-family:'Montserrat',sans-serif;color:var(--ink);background:var(--white);position:relative}
a{color:inherit;text-decoration:none}
.topbar{position:absolute;top:0;left:0;width:1200px;height:42px;background:var(--red);color:var(--white);font-size:14px;font-weight:500}
.topbar .contact{position:absolute;left:111px;top:12px;display:flex;gap:14px;align-items:center}
.topbar .social{position:absolute;right:110px;top:11px;display:flex;gap:8px}
.social-badge{width:20px;height:20px;border-radius:50%;background:var(--white);color:var(--red);font-size:8px;font-weight:700;display:flex;align-items:center;justify-content:center;font-style:normal}
.nav{position:absolute;top:42px;left:0;width:1200px;height:83px;background:var(--white);font-size:16px;font-weight:500}
.nav .left{position:absolute;left:111px;top:31px;display:flex;gap:30px}
.nav .right{position:absolute;right:111px;top:17px;display:flex;align-items:center;gap:18px}
.btn-outline{border:2px solid var(--red);border-radius:26px;padding:13px 18px;display:flex;gap:10px;align-items:center}
.brand{position:absolute;left:510px;top:42px;width:180px;height:142px;background:var(--white);border-radius:0 0 90px 90px;display:flex;align-items:center;justify-content:center;z-index:3}
.brand span{font-size:26px;font-weight:800;color:var(--red)}
.hero{position:absolute;top:125px;left:0;width:1200px;height:601px;background:linear-gradient(90deg,#2b2b2b 0%,#3a3a3a 45%,#4d3a2a 70%,#7a4a22 100%)}
.hero-text{position:absolute;left:112px;top:212px;color:var(--white)}
.hero-text h1{font-size:36px;font-weight:700;letter-spacing:.3px}
.hero-text p{font-size:18px;line-height:27px;margin-top:12px;width:500px}
.btn{display:inline-flex;align-items:center;justify-content:center;background:var(--red);color:var(--white);font-weight:700;border-radius:30px;font-size:15px}
.hero .btn{margin-top:24px;width:146px;height:51px;font-size:16px}
.arrow{position:absolute;top:290px}
.section-title{position:absolute;left:0;width:1200px;text-align:center;font-size:36px;font-weight:700}
.grid{position:absolute;left:111px;display:grid;grid-template-columns:repeat(3,310px);column-gap:23px;row-gap:19px}
.card{height:416px;background:var(--white);box-shadow:0 0 8px rgba(0,0,0,.14);border-radius:4px;position:relative;text-align:center}
.product-photo{position:absolute;left:85px;top:30px;width:140px;height:186px;border-radius:4px;background:linear-gradient(180deg,var(--placeholder-top),var(--placeholder-bottom))}
.card h3{position:absolute;top:237px;width:100%;font-size:22px;font-weight:700}
.stars{position:absolute;top:270px;width:100%;color:var(--star);font-size:14px;letter-spacing:2px}
.price{position:absolute;top:293px;width:100%;font-size:21px;font-weight:700}
.actions{position:absolute;top:336px;left:62px;display:flex;gap:12px}
.actions .btn{width:129px;height:43px}
.cart{width:45px;height:45px;border-radius:50%;box-shadow:0 0 6px rgba(0,0,0,.18);display:flex;align-items:center;justify-content:center}
.view-all{position:absolute;left:474px;top:1799px;width:252px;height:51px;gap:12px}
.promos{position:absolute;top:1947px;left:0;width:1200px;height:326px;display:flex}
.promo{width:400px;position:relative}
.promo .photo{height:243px}
.promo .bar{height:83px;color:var(--white);padding:18px 24px;position:relative}
.promo .bar b{font-size:18px;font-weight:700;display:block}
.promo .bar em{font-style:normal;font-size:16px;font-weight:700;color:var(--star);display:block;margin-top:6px}
.promo .bar u{position:absolute;right:26px;bottom:22px;font-size:12px;font-weight:600}
.newsletter{position:absolute;top:2927px;left:0;width:1200px;height:191px;background:var(--red);color:var(--white);text-align:center}
.newsletter h2{font-size:27px;font-weight:700;margin-top:40px}
.field{position:absolute;left:312px;top:100px;width:576px;height:47px;background:var(--white);border-radius:24px;text-align:left;color:#777;font-size:14px;padding:15px 22px}
.field .btn{position:absolute;right:4px;top:4px;width:136px;height:39px;font-size:15px}
.footer{position:absolute;top:3118px;left:0;width:1200px;height:274px;background:var(--dark);color:var(--white);font-size:15px}
.footer .fbrand{position:absolute;left:111px;top:72px;font-size:24px;font-weight:800;color:var(--red)}
.footer .fsocial{position:absolute;left:141px;top:161px;display:flex;gap:12px}
.fsocial .social-badge{width:34px;height:34px;font-size:11px}
.col{position:absolute;top:36px}
.col h4{font-size:18px;font-weight:600;margin-bottom:14px}
.col h4 span{color:var(--red)}
.col li{list-style:none;margin-bottom:7px;display:flex;gap:20px;align-items:flex-start;line-height:22px}
.bullet{width:12px;height:12px;border-radius:50%;background:var(--red);margin-top:5px;flex:none}
.rule{position:absolute;left:111px;top:220px;width:978px;height:1px;background:#555}
.copy{position:absolute;left:111px;top:236px;font-size:12px}
.cards{position:absolute;right:111px;top:229px;display:flex;gap:5px}
.cards i{width:50px;height:27px;background:#eee;border-radius:3px}
</style>
</head>
<body>
<svg width="0" height="0" style="position:absolute">
  <symbol id="cart-icon" viewBox="0 0 24 20"><path fill="#e31e24" d="M0 0h4l1 3h19l-3 9H7l1 2h14v2H6L3 2H0z"/><circle cx="8" cy="18" r="2" fill="#e31e24"/><circle cx="19" cy="18" r="2" fill="#e31e24"/></symbol>
</svg>
<header>
  <div class="topbar">
    <div class="contact">
      <svg width="13" height="13" viewBox="0 0 24 24"><path fill="#fff" d="M6.6 10.8a15 15 0 006.6 6.6l2.2-2.2c.3-.3.7-.4 1-.2 1.1.4 2.3.6 3.6.6.6 0 1 .4 1 1V20c0 .6-.4 1-1 1A17 17 0 013 4c0-.6.4-1 1-1h3.5c.6 0 1 .4 1 1 0 1.3.2 2.5.6 3.6.1.3 0 .7-.2 1z"/></svg>
      <span>+1 555-014-2276</span><span>|</span>
      <svg width="14" height="11" viewBox="0 0 24 18"><rect width="24" height="18" rx="2" fill="#fff"/><path d="M1 2l11 8 11-8" stroke="#e31e24" stroke-width="2" fill="none"/></svg>
      <span>hello@chompizsalsa.com</span>
    </div>
    <div class="social"><i class="social-badge" aria-label="Facelink">FL</i><i class="social-badge" aria-label="Snapgram">SG</i></div>
  </div>
  <nav class="nav">
    <div class="left"><a href="#">Home</a><a href="#">About Us</a><a href="#">Recipes</a></div>
    <div class="right">
      <a href="#">Contact Us</a><span>|</span>
      <svg width="15" height="15" viewBox="0 0 24 24"><circle cx="10" cy="10" r="7" stroke="#111" stroke-width="3" fill="none"/><path d="M15 15l6 6" stroke="#111" stroke-width="3"/></svg>
      <a href="#" class="btn-outline"><svg width="14" height="12"><use href="#cart-icon"/></svg>Buy Now</a>
    </div>
  </nav>
  <div class="brand"><span>CHOMP-IZ</span></div>
</header>

<section class="hero" role="img" aria-label="Bowls of salsa and guacamole with tortilla chips, tomatoes, lime and peppers on dark stone">
  <svg class="arrow" style="left:38px" width="16" height="30" viewBox="0 0 16 30"><path d="M14 2L2 15l12 13" stroke="#bbb" stroke-width="3" fill="none"/></svg>
  <svg class="arrow" style="right:38px" width="16" height="30" viewBox="0 0 16 30"><path d="M2 2l12 13L2 28" stroke="#fff" stroke-width="3" fill="none"/></svg>
  <div class="hero-text">
    <h1>WELCOME TO CHOMP-IZ SALSA</h1>
    <p>Lorem ipsum dolor sit amet, consectetur adipiscing elit sed do eiusmod tempor nostruda.</p>
    <a href="#" class="btn">SHOP NOW</a>
  </div>
</section>

<h2 class="section-title" style="top:812px">FEATURED PRODUCTS</h2>
<div class="grid" style="top:898px">
  <div class="card"><div class="product-photo" role="img" aria-label="Product photo of a salsa jar"></div><h3>PRODUCT TITLE</h3><div class="stars">★★★★★</div><div class="price">$19.00</div><div class="actions"><a class="btn" href="#">BUY NOW</a><span class="cart"><svg width="16" height="14"><use href="#cart-icon"/></svg></span></div></div>
  <div class="card"><div class="product-photo" role="img" aria-label="Product photo of a salsa jar"></div><h3>PRODUCT TITLE</h3><div class="stars">★★★★★</div><div class="price">$19.00</div><div class="actions"><a class="btn" href="#">BUY NOW</a><span class="cart"><svg width="16" height="14"><use href="#cart-icon"/></svg></span></div></div>
  <div class="card"><div class="product-photo" role="img" aria-label="Product photo of a salsa jar"></div><h3>PRODUCT TITLE</h3><div class="stars">★★★★★</div><div class="price">$19.00</div><div class="actions"><a class="btn" href="#">BUY NOW</a><span class="cart"><svg width="16" height="14"><use href="#cart-icon"/></svg></span></div></div>
  <div class="card"><div class="product-photo" role="img" aria-label="Product photo of a salsa jar"></div><h3>PRODUCT TITLE</h3><div class="stars">★★★★★</div><div class="price">$19.00</div><div class="actions"><a class="btn" href="#">BUY NOW</a><span class="cart"><svg width="16" height="14"><use href="#cart-icon"/></svg></span></div></div>
  <div class="card"><div class="product-photo" role="img" aria-label="Product photo of a salsa jar"></div><h3>PRODUCT TITLE</h3><div class="stars">★★★★★</div><div class="price">$19.00</div><div class="actions"><a class="btn" href="#">BUY NOW</a><span class="cart"><svg width="16" height="14"><use href="#cart-icon"/></svg></span></div></div>
  <div class="card"><div class="product-photo" role="img" aria-label="Product photo of a salsa jar"></div><h3>PRODUCT TITLE</h3><div class="stars">★★★★★</div><div class="price">$19.00</div><div class="actions"><a class="btn" href="#">BUY NOW</a><span class="cart"><svg width="16" height="14"><use href="#cart-icon"/></svg></span></div></div>
</div>
<a href="#" class="btn view-all">VIEW ALL PRODUCTS <svg width="14" height="14" viewBox="0 0 24 24"><circle cx="12" cy="12" r="11" fill="#fff"/><path d="M9 6l6 6-6 6" stroke="#e31e24" stroke-width="3" fill="none"/></svg></a>

<section class="promos">
  <div class="promo"><div class="photo" role="img" aria-label="Salsa jar beside soft tacos on a plate" style="background:linear-gradient(135deg,#6d5a45,#b9b0a0 60%,#d8cfa0)"></div><div class="bar" style="background:var(--brown)"><b>THE STANDARD LOREM</b><em>GET UO TO 50% OFF</em><u>SHOP NOW!</u></div></div>
  <div class="promo"><div class="photo" role="img" aria-label="Sizzling skillet of meat and vegetables with salsa jar" style="background:linear-gradient(135deg,#5a2e1a,#a0582a 50%,#c89a5a)"></div><div class="bar" style="background:var(--olive)"><b>THE STANDARD LOREM</b><em>GET UO TO 50% OFF</em><u>SHOP NOW!</u></div></div>
  <div class="promo"><div class="photo" role="img" aria-label="Tortilla chip dipped into a bowl of red salsa" style="background:linear-gradient(135deg,#e8e6e2,#d9d5cf 55%,#c0392b 85%)"></div><div class="bar" style="background:var(--red)"><b>THE STANDARD LOREM</b><em>GET UO TO 50% OFF</em><u>SHOP NOW!</u></div></div>
</section>

<h2 class="section-title" style="top:2358px">BEST SELLERS</h2>
<div class="grid" style="top:2446px">
  <div class="card"><div class="product-photo" role="img" aria-label="Product photo of a salsa jar"></div><h3>PRODUCT TITLE</h3><div class="stars">★★★★★</div><div class="price">$19.00</div><div class="actions"><a class="btn" href="#">BUY NOW</a><span class="cart"><svg width="16" height="14"><use href="#cart-icon"/></svg></span></div></div>
  <div class="card"><div class="product-photo" role="img" aria-label="Product photo of a salsa jar"></div><h3>PRODUCT TITLE</h3><div class="stars">★★★★★</div><div class="price">$19.00</div><div class="actions"><a class="btn" href="#">BUY NOW</a><span class="cart"><svg width="16" height="14"><use href="#cart-icon"/></svg></span></div></div>
  <div class="card"><div class="product-photo" role="img" aria-label="Product photo of a salsa jar"></div><h3>PRODUCT TITLE</h3><div class="stars">★★★★★</div><div class="price">$19.00</div><div class="actions"><a class="btn" href="#">BUY NOW</a><span class="cart"><svg width="16" height="14"><use href="#cart-icon"/></svg></span></div></div>
</div>

<section class="newsletter">
  <h2>Subscribe Our Newsletter</h2>
  <div class="field">Your Email Address<a href="#" class="btn">SUBSCRIBE</a></div>
</section>

<footer class="footer">
  <div class="fbrand">CHOMP-IZ</div>
  <div class="fsocial"><i class="social-badge" aria-label="Facelink">FL</i><i class="social-badge" aria-label="Snapgram">SG</i></div>
  <div class="col" style="left:373px"><h4><span>Useful</span> Links</h4><ul>
    <li><i class="bullet"></i>Home</li><li><i class="bullet"></i>About Us</li><li><i class="bullet"></i>Recipes</li><li><i class="bullet"></i>Buy Now</li><li><i class="bullet"></i>Contact Us</li></ul></div>
  <div class="col" style="left:634px"><h4><span>About</span> Links</h4><ul>
    <li><i class="bullet"></i>Site Map</li><li><i class="bullet"></i>FAQ</li><li><i class="bullet"></i>Privacy Policy</li><li><i class="bullet"></i>Terms Of Use</li></ul></div>
  <div class="col" style="left:884px"><h4><span>Contact</span> Us</h4><ul>
    <li><i class="bullet"></i>Lorem ipsum dolor sit,<br>Redmesa</li><li><i class="bullet"></i>+1 555-014-2276</li><li><i class="bullet"></i>hello@chompizsalsa.com</li></ul></div>
  <div class="rule"></div>
  <div class="copy">Copyrights 2021 Company Name. All Rights Reserved</div>
  <div class="cards"><i></i><i></i><i></i><i></i><i></i></div>
</footer>
</body>
</html>
```